2 Page Web Design Project (coded)

What does the company do?
Pilot contracting, flying private/corporate jets.

What is its target market?
The target market is primarily the private jet management market, i.e. companies, which specialize in private aircraft management and are looking to fill crew positions on a short/long term basis, usually on short notice basis

How many pages should your website include?
2 Pages: 1/ Front Page with Company Logo, 2/ Services and Contact page

Do you want coding included? YES

Do you have any style you would like your website to have?
The main colors of my logo should be kept. Please see attached business card logo.

Other Instructions: Please see Veltraxa's website (media section) for Skyrunner 812 pictures for free download, which can be incorporated into the website. Link: http://www.veltraxa.example/en/aerospace/media-centre/multimedia-library/details?categoryID=L3-Veltraxa%20Skyrunner%20812%20Aircraft.

Please see www.midairstaffingdesk.example for services description.
Find attached source file business card and use loge design/font for website, so both business card and website are consistent.

Requirements
Must have
• email link to link to my personal email, without giving my email address.

```html
<!DOCTYPE html>
<html lang="en">
<head>
<meta charset="utf-8">
<title>Corvane Crew</title>
<link rel="stylesheet" href="https://fonts.googleapis.com/css2?family=Arimo:wght@400;700&family=Pathway+Gothic+One&display=swap">
<style>
:root{
  --page:#f5f6f7;
  --blue:#1c5fa8;
  --blue-dark:#174f8e;
  --navy:#16365f;
  --footer:#1b4676;
  --link:#23549b;
  --cyan:#1a9ad6;
  --text:#666a6e;
  --heading:#4b4f53;
  --ink:#3a2e28;
  --ribbon:#2f2522;
  --line:#c9d3dc;
  --green:#6bb23a;
}
*{box-sizing:border-box;margin:0;padding:0}
html,body{width:1100px;height:1200px;overflow:hidden}
body{position:relative;background:var(--page);font-family:Arimo,Arial,sans-serif;color:var(--text)}
.abs{position:absolute}
a{color:inherit;text-decoration:none}

.main-nav{position:absolute;top:84px;font-size:19px;color:var(--link);display:flex;gap:18px}
.main-nav.left{left:87px;gap:19px}
.main-nav.right{left:718px;gap:17px}
.brand{position:absolute;left:380px;top:28px;width:320px;text-align:center}
.brand-mark{display:block;margin:0 auto 28px;width:26px;height:26px;border-radius:50%;background:var(--ink)}
.brand-name{font-size:30px;letter-spacing:1px;color:var(--ink);font-weight:400;line-height:32px}

.hero-band{position:absolute;left:0;top:112px}
.hero-copy{position:absolute;left:129px;top:168px;width:345px;height:118px;background:rgba(43,110,185,.75);padding:16px 16px;color:#e8f1fb;font-family:"Pathway Gothic One",Arial,sans-serif;font-size:19px;line-height:28px}
.hero-copy .lead{font-family:Arimo,Arial,sans-serif;font-size:16px}
.hero-btn{position:absolute;left:136px;top:295px;width:128px;height:25px;border-radius:13px;background:var(--navy);color:#fff;font-style:italic;font-size:12px;line-height:25px;padding-left:14px}
.hero-btn i{position:absolute;right:4px;top:4px;width:17px;height:17px;border-radius:50%;background:#5ec3ef}
.hero-frame{position:absolute;left:555px;top:157px;width:369px;height:243px;background:#fff;border-radius:6px;padding:6px;box-shadow:0 6px 14px rgba(0,0,0,.25)}
.hero-photo{width:100%;height:100%;background:linear-gradient(135deg,#3b2a1c 0%,#8a6a4a 35%,#d9c4a2 60%,#b39268 100%)}
.slide-arrow{position:absolute;top:347px;width:42px;height:42px;border-radius:50%;background:#fff;box-shadow:0 0 0 4px rgba(255,255,255,.4),0 2px 4px rgba(0,0,0,.2)}
.slide-arrow svg{position:absolute;left:13px;top:13px}

.card{position:absolute;top:453px;width:203px;height:183px;background:#fff;border:1px solid #d5dadf;border-radius:3px;padding:0 17px}
.card h3{margin-top:9px;font-size:21px;font-weight:400;color:var(--heading);height:44px;line-height:24px}
.card p{font-size:12px;line-height:16px;letter-spacing:-0.3px;text-align:justify;margin-bottom:16px;position:relative}
.card p a{position:absolute;right:0;bottom:0;font-size:11px;letter-spacing:0;color:var(--link);text-decoration:underline}
.card .folder{position:absolute;right:12px;top:-35px;width:74px;height:76px;background:linear-gradient(135deg,#e8c987,#c49a52);border-radius:3px}
.ribbon{position:absolute;left:124px;top:168px;width:99px;height:35px;background:var(--ribbon);color:#fff;font-size:14px;line-height:35px;padding-left:6px;clip-path:polygon(0 0,88% 0,100% 50%,88% 100%,0 100%);border-radius:6px 0 0 6px}

.divider{position:absolute;left:115px;top:692px;width:830px;height:1px;background:linear-gradient(90deg,transparent,#d0d5da,transparent)}
.section-title{position:absolute;font-size:20px;font-weight:400;color:var(--heading);padding-bottom:6px;border-bottom:1px solid var(--line)}
.about p{font-size:12px;line-height:16px;letter-spacing:-0.1px;text-align:justify;margin-bottom:11px}

.login label.field{position:absolute;font-size:14px;font-weight:700;color:#9a9ea2}
.login .input{position:absolute;left:701px;width:290px;height:38px;background:#d8dbde;padding:4px}
.login .input span{display:block;height:100%;border:1px solid #c7c9c0}
.login .small-link{position:absolute;right:114px;font-size:13px;color:var(--cyan)}
.login-btn{position:absolute;left:895px;top:877px;width:92px;height:32px;background:linear-gradient(#8cc94f,var(--green));border:1px solid #5a9a2e;border-radius:3px;color:#fff;font-weight:700;font-size:13px;line-height:30px;padding-left:12px}
.login-btn svg{position:absolute;right:12px;top:9px}

.footer{position:absolute;left:0;top:975px;width:1100px;height:225px;background:linear-gradient(#1e4f84,var(--footer));color:#fff}
.footer h4{position:absolute;top:37px;font-size:18px;font-weight:400}
.footer ul{position:absolute;top:76px;list-style:none;font-size:11px}
.footer li{height:25px}
.footer address{position:absolute;left:549px;top:74px;font-style:normal;font-size:14px;line-height:20px}
.social{position:absolute;width:44px;height:44px;border-radius:50%;background:#3b8fd0;box-shadow:0 2px 4px rgba(0,0,0,.3)}
</style>
</head>
<body>

<nav class="main-nav left"><a href="#">home</a><a href="#">about us</a><a href="#">our services</a></nav>
<div class="brand"><span class="brand-mark"></span><span class="brand-name">CORVANE CREW</span></div>
<nav class="main-nav right"><a href="#">solutions</a><a href="#">work with us</a><a href="#">contact us</a></nav>

<svg class="hero-band" width="1100" height="270" viewBox="0 0 1100 270" aria-hidden="true">
  <defs><linearGradient id="band" x1="0" y1="0" x2="0" y2="1"><stop offset="0" stop-color="#1a5598"/><stop offset="1" stop-color="#1f66b4"/></linearGradient></defs>
  <path d="M0 6 Q300 30 560 18 T1100 6 L1100 232 Q800 250 560 242 Q250 232 0 262 Z" fill="url(#band)"/>
</svg>

<div class="hero-copy"><span class="lead">Lorem ipsum dolor sit amet, consectetur</span><br>adipisicing elit, sed do eiusmod tempor incididunt ut labore et dolore magna aliqua.</div>
<a class="hero-btn" href="#">Go to Services<i></i></a>
<div class="hero-frame"><div class="hero-photo" role="img" aria-label="Private jet cabin interior with leather seats and wood table"></div></div>
<div class="slide-arrow" style="left:67px"><svg width="16" height="16" viewBox="0 0 16 16"><path d="M8 3 3 8l5 5M13 3 8 8l5 5" stroke="#333" stroke-width="2" fill="none"/></svg></div>
<div class="slide-arrow" style="left:980px"><svg width="16" height="16" viewBox="0 0 16 16"><path d="M3 3l5 5-5 5M8 3l5 5-5 5" stroke="#333" stroke-width="2" fill="none"/></svg></div>

<div class="card" style="left:73px">
  <div class="folder" role="img" aria-label="Folder icon with documents"></div>
  <h3>Solutions</h3>
  <p>Lorem ipsum dolor sit amet, consectetur adipisicing elit, sed do eiusmod.<a href="#">more</a></p>
  <p>Lorem ipsum dolor sit amet, consectetur adipisicing elit, sed do eiusmod.<a href="#">more</a></p>
  <a class="ribbon" href="#">VIEW MORE</a>
</div>
<div class="card" style="left:308px">
  <div class="folder" role="img" aria-label="Folder icon with application cards"></div>
  <h3>Join Us</h3>
  <p>Lorem ipsum dolor sit amet, consectetur adipisicing elit, sed do eiusmod.<a href="#">apply now</a></p>
  <p>Lorem ipsum dolor sit amet, consectetur adipisicing elit, sed do eiusmod.<a href="#">apply now</a></p>
  <a class="ribbon" href="#">VIEW MORE</a>
</div>
<div class="card" style="left:544px">
  <div class="folder" role="img" aria-label="Folder icon with team window"></div>
  <h3>Our Team</h3>
  <p>Lorem ipsum dolor sit amet, consectetur adipisicing elit, sed do eiusmod.<a href="#">more</a></p>
  <p>Lorem ipsum dolor sit amet, consectetur adipisicing elit, sed do eiusmod.<a href="#">more</a></p>
  <a class="ribbon" href="#">VIEW MORE</a>
</div>
<div class="card" style="left:780px">
  <div class="folder" role="img" aria-label="Folder icon with review papers"></div>
  <h3>Reviews</h3>
  <p>Lorem ipsum dolor sit amet, consectetur adipisicing elit, sed do eiusmod.<a href="#">more</a></p>
  <p>Lorem ipsum dolor sit amet, consectetur adipisicing elit, sed do eiusmod.<a href="#">more</a></p>
  <a class="ribbon" href="#">VIEW MORE</a>
</div>

<div class="divider"></div>

<h2 class="section-title" style="left:73px;top:713px;width:462px;padding-left:3px">Who we are?</h2>
<div class="about abs" style="left:76px;top:757px;width:454px">
  <p>Lorem ipsum dolor sit amet, consectetur adipisicing elit, sed do eiusmod tempor incididunt ut labore et dolore magna aliqua. Ut enim ad minim veniam, quis nostrud exercitation ullamco laboris nisi ut aliquip ex ea commodo consequat. Duis aute irure dolor in reprehenderit in voluptate velit esse cillum dolore eu fugiat nulla pariatur. Excepteur sint occaecat cupidatat non proident, sunt in culpa qui officia deserunt mollit anim id est laborum.</p>
  <p>Lorem ipsum dolor sit amet, consectetur adipisicing elit, sed do eiusmod tempor incididunt ut labore et dolore magna aliqua. Ut enim ad minim veniam, quis nostrud exercitation ullamco laboris nisi ut aliquip ex ea commodo consequat. Ut enim ad minim veniam, quis nostrud exercitation ullamco laboris nisi ut aliquip ex ea commodo consequat.</p>
</div>

<div class="login">
  <h2 class="section-title" style="left:606px;top:713px;width:385px;padding-left:3px">User Login</h2>
  <a class="small-link" href="#" style="top:750px">Forgot username?</a>
  <label class="field" style="left:610px;top:779px">Username:</label>
  <div class="input" style="top:769px"><span style="background:#fbfbea"></span></div>
  <a class="small-link" href="#" style="top:812px">Forgot password?</a>
  <label class="field" style="left:608px;top:842px">Password:</label>
  <div class="input" style="top:831px"><span style="background:#fff"></span></div>
  <div class="abs" style="left:706px;top:881px;font-size:13px;color:#999"><span style="display:inline-block;width:12px;height:12px;border:1px solid #999;border-radius:2px;vertical-align:-2px;margin-right:4px"></span>Remember me</div>
  <a class="login-btn" href="#">Log In<svg width="18" height="12" viewBox="0 0 18 12"><path d="M1 4h9V0l7 6-7 6V8H1z" fill="#fff"/></svg></a>
  <div class="abs" style="left:606px;top:920px;width:385px;height:1px;background:var(--line)"></div>
  <div class="abs" style="left:606px;top:929px;font-size:16px;color:#555">Don’t have an account?</div>
  <a class="abs" href="#" style="left:890px;top:930px;font-size:13px;color:var(--cyan);text-decoration:underline">Create one here.</a>
</div>

<footer class="footer">
  <h4 style="left:83px">Footer link</h4>
  <ul style="left:83px"><li>Footer link</li><li>Footer link</li><li>Footer link</li><li>Footer link</li><li>Footer link</li></ul>
  <h4 style="left:316px">Footer link</h4>
  <ul style="left:316px"><li>Footer link</li><li>Footer link</li><li>Footer link</li><li>Footer link</li><li>Footer link</li></ul>
  <h4 style="left:549px">Contact Us</h4>
  <address>27 Harlow Quay Road,<br>Westbrook, ON,<br>K4M7T2 Canada</address>
  <h4 style="left:813px">Connect Us With :</h4>
  <a class="social" href="#" aria-label="Social network 1" style="left:811px;top:77px"></a>
  <a class="social" href="#" aria-label="Social network 2" style="left:869px;top:77px"></a>
  <a class="social" href="#" aria-label="Social network 3" style="left:929px;top:77px"></a>
  <a class="social" href="#" aria-label="Social network 4" style="left:815px;top:134px"></a>
  <a class="social" href="#" aria-label="Social network 5" style="left:874px;top:134px;background:#c8322a"></a>
  <a class="social" href="#" aria-label="Social network 6" style="left:927px;top:134px"></a>
</footer>

</body>
</html>
```